Storm Restoration Contractor needs a professional letterhead design

Looking for a professional letterhead design. Not looking for your cheapo MS Word standard ones that are readily available. Dont want it to be cookie cutter look like ones readily available online. We just recently changed our logo and want to freshen up all our documents. Our company handles restoring a property back to a pre-loss condition after a storm damages it. For example, wind, hail, flood, fire losses.

Target Market(s)

Property Owners, Homeowners, Property Owners, Commercial Property Owners, Property Management Companies

Industry/Entity Type

Construction Company

Requirements
Must have
• Professional, Use 1 of 2 logo options
• Storm Restoration, Roofing, Siding, Windows

```html
<!DOCTYPE html>
<html lang="en">
<head>
<meta charset="UTF-8">
<title>Northgate Exteriors Letterhead</title>
<link href="https://fonts.googleapis.com/css2?family=Open+Sans:wght@400;700&display=swap" rel="stylesheet">
<style>
  :root {
    --backdrop: #e4e4e4;
    --paper: #ffffff;
    --brand-blue: #1a78c6;
    --brand-charcoal: #4a4a4c;
    --ink: #3a3a3a;
  }
  * { margin: 0; padding: 0; box-sizing: border-box; }
  html, body {
    width: 1200px; height: 1200px; overflow: hidden;
    background: var(--backdrop);
    font-family: "Open Sans", Arial, sans-serif;
  }
  .letterhead {
    position: absolute; left: 197px; top: 30px;
    width: 806px; height: 1140px;
    background: var(--paper);
    box-shadow: 0 4px 18px rgba(0,0,0,0.12);
  }
  .top-rule-blue {
    position: absolute; left: 0; top: 0;
    width: 612px; height: 7px;
    background: var(--brand-blue);
  }
  .top-rule-charcoal {
    position: absolute; left: 612px; top: 0;
    width: 194px; height: 14px;
    background: var(--brand-charcoal);
  }
  .brand {
    position: absolute; left: 56px; top: 92px;
    display: flex; align-items: center; gap: 14px;
  }
  .brand-dot {
    width: 58px; height: 58px; border-radius: 50%;
    border: 5px solid var(--brand-blue);
  }
  .brand-divider {
    width: 2px; height: 66px; background: var(--brand-blue);
  }
  .brand-name {
    color: var(--brand-blue);
    font-weight: 700; font-size: 27px; line-height: 1.05;
    letter-spacing: 2px; text-transform: uppercase;
  }
  .contact {
    position: absolute; left: 640px; top: 48px;
    list-style: none; font-size: 10.5px; color: var(--ink); line-height: 16px;
  }
  .contact li { display: flex; align-items: center; gap: 6px; }
  .contact svg { width: 9px; height: 9px; fill: var(--brand-blue); flex: none; }
</style>
</head>
<body>
  <main class="letterhead">
    <div class="top-rule-blue"></div>
    <div class="top-rule-charcoal"></div>

    <header class="brand">
      <div class="brand-dot"></div>
      <div class="brand-divider"></div>
      <div class="brand-name">Northgate<br>Exteriors</div>
    </header>

    <ul class="contact">
      <li><svg viewBox="0 0 10 10"><path d="M2 0.5 L3.6 0.5 L4.2 3 L3 3.8 C3.6 5.2 4.8 6.4 6.2 7 L7 5.8 L9.5 6.4 L9.5 8 C9.5 9 8.7 9.5 8 9.5 C4 9.2 0.8 6 0.5 2 C0.5 1.3 1 0.5 2 0.5Z"/></svg>555-014-2200</li>
      <li><svg viewBox="0 0 10 10"><rect x="2.5" y="0.5" width="5" height="3"/><rect x="0.5" y="3.5" width="9" height="4" rx="1"/><rect x="2.5" y="6.5" width="5" height="3"/></svg>555-014-2290</li>
      <li><svg viewBox="0 0 10 10"><path d="M0.5 2 H9.5 V8 H0.5Z M0.5 2 L5 5.5 L9.5 2" fill="none" stroke="#1a78c6" stroke-width="1.2"/></svg>info@northgateext.com</li>
      <li><svg viewBox="0 0 10 10"><circle cx="5" cy="5" r="4.3" fill="none" stroke="#1a78c6" stroke-width="1"/><path d="M0.7 5 H9.3 M5 0.7 C3 3 3 7 5 9.3 M5 0.7 C7 3 7 7 5 9.3" fill="none" stroke="#1a78c6" stroke-width="0.8"/></svg>www.northgateext.com</li>
    </ul>
  </main>
</body>
</html>
```